Tech business card design

We need an amazing business card design for our new business 'Pexla' a marketing tech startup based in Sydney, Australia. We provide an online marketplace for businesses to search and buy advertising media, connect with service providers and learn more about marketing. We wish to communicate 'cool tech', reliability and professionalism and design based around our logo.

Target Market(s)

Business Owners

Contact Information for Business Card

Name
Position
Email Address
Website
Phone Number

Font styles to use
Other font styles liked:
• Avenir & Avenir Next

Colors

Designer to choose colors to be used in the design.

```html
<!DOCTYPE html>
<html lang="en">
<head>
<meta charset="utf-8">
<title>Pexla Business Card</title>
<link rel="stylesheet" href="https://fonts.googleapis.com/css2?family=Nunito+Sans:wght@400;800&display=swap">
<style>
  :root {
    --backdrop: #3b3b3d;
    --card-front: #0d0d0e;
    --card-back: #0f1238;
    --ink: #ffffff;
    --ink-soft: #e4e6f2;
  }
  html, body {
    margin: 0;
    padding: 0;
    width: 1200px;
    height: 1000px;
    overflow: hidden;
    background: var(--backdrop);
    font-family: "Nunito Sans", sans-serif;
  }
  .canvas {
    position: relative;
    width: 1200px;
    height: 1000px;
  }
  .card {
    position: absolute;
    left: 240px;
    width: 720px;
    height: 412px;
    border-radius: 28px;
    box-shadow: 0 18px 40px rgba(0, 0, 0, 0.45);
  }
  .card-front {
    top: 58px;
    background: var(--card-front);
    display: flex;
    align-items: center;
    justify-content: center;
  }
  .card-back {
    top: 530px;
    background: var(--card-back);
  }
  .wordmark {
    color: var(--ink);
    font-weight: 800;
    letter-spacing: -2px;
    line-height: 1;
  }
  .card-front .wordmark {
    font-size: 150px;
  }
  .card-back .wordmark {
    position: absolute;
    left: 56px;
    top: 160px;
    font-size: 96px;
  }
  .divider {
    position: absolute;
    left: 352px;
    top: 118px;
    width: 2px;
    height: 196px;
    background: var(--ink-soft);
  }
  .contact {
    position: absolute;
    left: 380px;
    top: 120px;
    color: var(--ink);
  }
  .contact-name {
    margin: 0;
    font-size: 30px;
    font-weight: 400;
    line-height: 1.1;
  }
  .contact-role {
    margin: 2px 0 26px;
    font-size: 18px;
    font-weight: 400;
    color: var(--ink-soft);
  }
  .contact-list {
    list-style: none;
    margin: 0;
    padding: 0;
  }
  .contact-item {
    display: flex;
    align-items: center;
    gap: 10px;
    font-size: 19px;
    margin-bottom: 8px;
  }
  .contact-icon {
    width: 24px;
    height: 24px;
    flex: none;
  }
</style>
</head>
<body>
<main class="canvas">
  <section class="card card-front" aria-label="Card front">
    <span class="wordmark">pexla</span>
  </section>

  <section class="card card-back" aria-label="Card back">
    <span class="wordmark">pexla</span>
    <div class="divider"></div>
    <div class="contact">
      <h1 class="contact-name">Marcus Lane</h1>
      <p class="contact-role">Managing Director</p>
      <ul class="contact-list">
        <li class="contact-item">
          <svg class="contact-icon" viewBox="0 0 24 24" fill="none" stroke="#fff" stroke-width="1.4">
            <circle cx="12" cy="12" r="11"/>
            <rect x="8.5" y="5.5" width="7" height="13" rx="1.2"/>
            <line x1="11" y1="16.3" x2="13" y2="16.3"/>
          </svg>
          <span>800-415-0027</span>
        </li>
        <li class="contact-item">
          <svg class="contact-icon" viewBox="0 0 24 24" fill="none" stroke="#fff" stroke-width="1.4">
            <circle cx="12" cy="12" r="11"/>
            <rect x="6" y="8" width="12" height="8.5" rx="1"/>
            <polyline points="6,8.5 12,13 18,8.5"/>
          </svg>
          <span>marcus@pexlamail.com</span>
        </li>
        <li class="contact-item">
          <svg class="contact-icon" viewBox="0 0 24 24" fill="none" stroke="#fff" stroke-width="1.4">
            <circle cx="12" cy="12" r="11"/>
            <circle cx="12" cy="12" r="6.5"/>
            <ellipse cx="12" cy="12" rx="2.8" ry="6.5"/>
            <line x1="5.5" y1="12" x2="18.5" y2="12"/>
          </svg>
          <span>www.pexla.com</span>
        </li>
      </ul>
    </div>
  </section>
</main>
</body>
</html>
```